A4 4-sided brochure - medical specialist

A4 sized, 4 sided brochure, glossy. I am a medical specialist (urologist) and need a brochure to hand out to GPs. I will write all text and will send photos. I have attached an example of the kind of thing I was thinking of. My website is https://www.harbourpointclinic.com.au/
There are three of us in a group but the brochure is just for me.
It is to give to GPs and not direct to patients, so should tell the GPs why they should refer to me.
Target Market(s)
Medical
Industry/Entity Type
medicine - surgery - urology
Requirements
Must have
- I have uploaded an outline of the layout with files that are listed on the outline - please load them up as indicated and submit your designs
Should not have
- Claims that I am the best

```html
<!DOCTYPE html>
<html lang="en">
<head>
<meta charset="utf-8">
<title>Harbour Point Clinic – GP Brochure</title>
<link href="https://fonts.googleapis.com/css2?family=Poppins:ital,wght@0,400;0,500;0,600;0,700;0,800;1,400;1,500&display=swap" rel="stylesheet">
<style>
:root{
  --navy:#1b3c69;
  --navy-deep:#15305a;
  --sky:#4a93dc;
  --sky-soft:#6fb0ee;
  --ink:#1f2b3d;
  --paper:#ffffff;
  --backdrop:#eceae8;
  --pill:#1c3a66;
}
*{box-sizing:border-box;margin:0;padding:0}
html,body{width:1200px;height:3277px;overflow:hidden}
body{background:var(--backdrop);font-family:'Poppins',sans-serif;color:var(--ink);position:relative}
.spread{position:absolute;left:60px;width:1080px;height:761px;background:var(--paper);box-shadow:0 10px 30px rgba(0,0,0,.18);overflow:hidden}
.spread--outer{top:837px}
.spread--inner{top:1678px}
.page{position:absolute;top:0;width:540px;height:761px}
.page--left{left:0}
.page--right{left:540px}
.abs{position:absolute}
.ph{position:absolute;border-radius:6px}
/* about */
.about{background:var(--navy)}
.about .portrait{left:36px;top:40px;width:180px;height:180px;background:linear-gradient(160deg,#8ea2b8,#2d3d52);border:3px solid var(--sky-soft)}
.title{font-weight:600;font-size:22px;letter-spacing:.3px}
.title span{color:var(--sky)}
.about .title{left:236px;top:30px;color:#fff}
.about .title span{color:var(--sky-soft)}
.about .bio{left:236px;top:72px;width:280px;color:#fff;font-size:9px;line-height:1.45}
.about .bio p{margin-bottom:10px}
.pill{display:inline-block;background:var(--pill);color:#fff;font-size:9.5px;font-weight:600;padding:4px 14px;border-radius:12px;border:1px solid rgba(255,255,255,.25);white-space:nowrap}
.pill b{color:var(--sky-soft);font-weight:600}
.ticks{list-style:none;font-size:8.4px;line-height:1.35;color:#fff}
.ticks li{position:relative;padding-left:14px;margin-bottom:5px}
.ticks li::before{content:"✔";position:absolute;left:0;top:0;color:var(--sky-soft);font-size:8px}
.about .col-a{left:36px;top:245px;width:250px}
.about .col-b{left:310px;top:245px;width:215px}
.about .col-a .pill,.about .col-b .pill{margin-bottom:10px}
.contact-card{left:36px;top:636px;width:480px;height:125px;background:var(--sky)}
.contact-tab{left:36px;top:610px;height:30px;background:var(--sky);color:#fff;font-weight:600;font-size:11.5px;padding:7px 18px;border-radius:6px 6px 0 0}
.call{color:#fff;font-size:8px;line-height:1.1}
.call strong{display:block;font-size:13px;font-weight:500}
.phone{display:inline-flex;align-items:center;gap:4px;background:var(--navy);color:#fff;font-weight:600;font-size:12px;border-radius:14px;padding:3px 14px;border:1.5px solid #fff;white-space:nowrap}
.phone svg{width:10px;height:10px}
.or{color:#fff;font-weight:600;font-size:12px}
.contact-icons{left:0;top:58px;width:480px;display:flex}
.contact-icons div{flex:1;text-align:center;color:#fff;font-size:8px;border-right:1px solid rgba(255,255,255,.35)}
.contact-icons div:last-child{border-right:none}
.contact-icons svg{display:block;margin:0 auto 8px;width:26px;height:26px}
/* cover */
.cover .brand{left:0;top:60px;width:540px;text-align:center}
.brand-dot{display:block;width:46px;height:46px;margin:0 auto 10px;border-radius:50%;border:3px solid var(--sky)}
.brand-name{font-size:21px;font-weight:500;color:var(--navy);letter-spacing:.2px}
.brand-sub{font-size:8px;color:var(--sky);letter-spacing:6px;margin-top:1px}
.cover .headline{left:0;top:168px;width:540px;text-align:center;color:var(--ink)}
.headline .l1{font-weight:600;font-size:23px;line-height:1.15}
.headline .big{font-weight:800;font-size:44px;color:var(--navy);line-height:1.05;letter-spacing:.5px}
.headline .prob{font-weight:600;font-size:19px;color:var(--sky);letter-spacing:12px;line-height:1}
.headline .band{display:inline-block;margin-top:4px;background:var(--navy);color:#fff;font-size:11px;font-weight:600;padding:3px 18px;border-radius:10px}
.cover .hero{left:0;top:344px;width:540px;height:320px;border-radius:0;background:linear-gradient(120deg,#eef3f8 0%,#c9d7e6 45%,#2a4a73 100%)}
.footer-band{left:0;top:664px;width:540px;height:97px;background:var(--navy);display:flex;align-items:center;justify-content:center;color:#fff;font-weight:600;font-size:17px;letter-spacing:1.5px}
/* values */
.values .title{left:36px;top:28px;color:var(--navy)}
.values .lead{left:36px;top:68px;width:235px;font-size:8.4px;line-height:1.4;color:var(--navy)}
.values .approach{left:36px;top:142px;width:240px;font-size:10px;font-weight:600;line-height:1.35;color:var(--ink)}
.values .people{left:290px;top:40px;width:212px;height:180px;background:linear-gradient(150deg,#d9e6f2,#9bb5cf 60%,#5a7391);border:2px solid var(--navy)}
.values .ticks{color:var(--navy);font-size:8.2px}
.values .ticks li::before{color:var(--sky)}
.values .vl{left:36px;top:232px;width:205px}
.values .vr{left:283px;top:232px;width:215px}
.diagram{position:absolute;width:148px;height:132px;border:2px solid var(--navy);border-radius:12px;background:linear-gradient(150deg,#f6ecea,#e7c4bd 55%,#d48c7d)}
.inner-rule{left:0;top:722px;width:540px;height:18px;background:var(--navy)}
/* gps */
.gps .organs{left:36px;top:36px;width:468px;height:180px;border:2px solid var(--navy);border-radius:14px;background:linear-gradient(120deg,#cfe1f2,#e6eef6 40%,#d9737a 70%,#b9d3ea)}
.gps .title{left:36px;top:232px;color:var(--navy);font-size:21px}
.gps .title span{font-weight:800;font-size:30px;color:var(--sky)}
.gps .pill{font-size:9px;padding:4px 12px}
.gps-links{left:36px;top:290px;width:470px;display:flex;gap:14px}
.gps .small-tick{font-size:8px;color:var(--navy);margin:8px 0 0 8px}
.gps .small-tick::before{content:"✔ ";color:var(--sky)}
.gps .ticks{color:var(--navy);font-size:8.2px}
.gps .ticks li{margin-bottom:3px}
.gps .ticks li::before{color:var(--sky)}
.problems-a{left:36px;top:396px;width:140px}
.problems-b{left:184px;top:396px;width:186px}
.gps .kidneys{left:392px;top:360px;width:128px;height:240px;border-radius:24px;background:linear-gradient(180deg,#f3dfe0 0%,#e8a3a0 35%,#f0b57a 70%,#fbeee2 100%)}
.gps-contact{left:36px;top:650px;width:470px;height:52px;background:var(--sky);display:flex;align-items:center;gap:12px;padding-left:12px}
.gps-footer{left:0;top:706px;width:540px;height:55px;background:var(--navy);display:flex;align-items:center;justify-content:center;color:#fff;font-weight:600;font-size:17px;letter-spacing:1.5px}
</style>
</head>
<body>

<section class="spread spread--outer">
  <div class="page page--left about">
    <div class="ph portrait" role="img" aria-label="Portrait photo of Dr Daniel Hartley in a suit"></div>
    <h2 class="abs title">ABOUT <span>DANIEL HARTLEY</span></h2>
    <div class="abs bio">
      <p>A/Prof Daniel Hartley is a consultant urologist with private practice at Northgate Private and Westbrook Hospital. Daniel consults at Northgate, the Hills, and the South Coast, and undertakes Day Case lists at Shellcove and Millbrook. He is Associate Professor at Bayview University &amp; was senior staff specialist for 14 years at Bayview Royal Hospital.</p>
      <p>Daniel is also a high-volume robotic and open cancer surgeon, and performs brachytherapy for prostate cancer, so is able to offer patients all current options for urology cancer treatment.</p>
    </div>
    <div class="abs col-a">
      <span class="pill"><b>AREAS</b> OF INTEREST</span>
      <ul class="ticks">
        <li>PSA management</li>
        <li>BPH/LUTS medical and surgical treatment including laser, prostatic lift and steam therapy</li>
        <li>UTI and haematuria assessment</li>
        <li>Kidney stone surgery and biochemical management</li>
        <li>Vasectomy and vasectomy reversal</li>
        <li>Robotic surgery, brachytherapy, and focal therapy for prostate cancer</li>
        <li>Robotic, open, and laparoscopic urology cancer surgery</li>
        <li>Software fusion prostate biopsy</li>
        <li>Erectile dysfunction and incontinence</li>
        <li>Urodynamic investigation and female incontinence</li>
        <li>PTNS and Pharmaceutical neurotoxin management for overactive bladder</li>
        <li>Urinary tract infection management</li>
        <li>MRI-guided prostate biopsy</li>
        <li>Bladder cancer management</li>
        <li>Retroperitoneal lymph node dissection for testis cancer</li>
      </ul>
    </div>
    <div class="abs col-b">
      <span class="pill"><b>PROFESSIONAL</b> QUALIFICATIONS</span>
      <ul class="ticks">
        <li>Bachelor of Science (1st Class Hons) Northfield University</li>
        <li>Master of Science, Kingsport University</li>
        <li>Bachelor of Medicine, Kingsport University</li>
        <li>Doctor of Medicine, Ashwell University</li>
        <li>Fellow of the College of Surgical Practice (Urology)</li>
        <li>Fellow of the Australasian Surgical College (Urology)</li>
      </ul>
      <span class="pill" style="margin-top:6px"><b>PROFESSIONAL</b> MEMBERSHIPS</span>
      <ul class="ticks">
        <li>FRCS(Urol)</li>
        <li>FRACS(Urol)</li>
        <li>Regional Urology Society</li>
        <li>Prostate Research Trials Network</li>
        <li>Urological Oncology Forum</li>
        <li>International Urology Council</li>
        <li>Continental Urology Association</li>
      </ul>
    </div>
    <div class="abs contact-tab">A/Prof Daniel Hartley – Urologist</div>
    <div class="abs contact-card">
      <div class="abs" style="left:16px;top:14px;display:flex;align-items:center;gap:12px">
        <div class="call">Call to<strong>Daniel Hartley</strong></div>
        <span class="or">-</span>
        <span class="phone"><svg viewBox="0 0 10 10"><path d="M2 1c1 0 1.5 2 1 2.5L2.5 4c.5 1.3 2 2.8 3.5 3.5l.5-.5C7 6.5 9 7 9 8s-1 1.5-2 1.5C4 9.5.5 6 .5 3 .5 2 1 1 2 1z" fill="#fff"/></svg>0400 118 204</span>
        <span class="or">OR</span>
        <span class="phone"><svg viewBox="0 0 10 10"><path d="M2 1c1 0 1.5 2 1 2.5L2.5 4c.5 1.3 2 2.8 3.5 3.5l.5-.5C7 6.5 9 7 9 8s-1 1.5-2 1.5C4 9.5.5 6 .5 3 .5 2 1 1 2 1z" fill="#fff"/></svg>0400 118 597</span>
      </div>
      <div class="abs contact-icons">
        <div><svg viewBox="0 0 26 26"><circle cx="13" cy="13" r="12" fill="none" stroke="#fff" stroke-width="1.5"/><rect x="8" y="8" width="10" height="11" rx="1" fill="#fff"/></svg>08 5550 2190</div>
        <div><svg viewBox="0 0 26 26"><circle cx="13" cy="13" r="12" fill="none" stroke="#fff" stroke-width="1.5"/><rect x="7" y="9" width="12" height="8" rx="1" fill="#fff"/><path d="M7 9l6 5 6-5" stroke="#4a93dc" fill="none"/></svg>reception@harbourpointclinic.com.au</div>
        <div><svg viewBox="0 0 26 26"><circle cx="13" cy="13" r="12" fill="none" stroke="#fff" stroke-width="1.5"/><circle cx="13" cy="13" r="6" fill="none" stroke="#fff" stroke-width="1.4"/><path d="M7 13h12M13 7c-3 3-3 9 0 12M13 7c3 3 3 9 0 12" stroke="#fff" fill="none"/></svg>www.harbourpointclinic.com.au</div>
      </div>
    </div>
  </div>

  <div class="page page--right cover">
    <div class="abs brand">
      <span class="brand-dot"></span>
      <div class="brand-name">Harbour Point Clinic</div>
      <div class="brand-sub">BAYVIEW</div>
    </div>
    <div class="abs headline">
      <div class="l1">I AM HERE TO<br>SOLVE YOUR COMPLEX</div>
      <div class="big">UROLOGICAL</div>
      <div class="prob">PROBLEM</div>
      <div class="band">WITH HIGH QUALITY CARE &amp; RAPID ACCESS</div>
    </div>
    <div class="ph hero" role="img" aria-label="Photo of the urologist in consultation with a patient, reviewing scans on a laptop"></div>
    <div class="abs footer-band">www.harbourpointclinic.com.au</div>
  </div>
</section>

<section class="spread spread--inner">
  <div class="page page--left values">
    <h2 class="abs title">OUR <span>VALUES</span></h2>
    <p class="abs lead">We are aware that you have many choices in who provides your health care, and we appreciate that you are putting your trust in us.</p>
    <p class="abs approach">Our approach to your care governs everything we do for you, and it consists of the following elements:</p>
    <div class="ph people" role="img" aria-label="Photo of a smiling older couple"></div>
    <ul class="abs ticks vl">
      <li>We want you to feel comfortable with all of our staff, and we will make every effort to make your visits as stress free as possible.</li>
      <li>We recognise that each patient is an individual with different needs.</li>
      <li>We want to work in partnership with you so that you are actively involved in decisions about your care. Our role is to give you options for treatment and advice, and for you to make the decision that you feel most comfortable with, with our guidance if necessary.</li>
    </ul>
    <ul class="abs ticks vr">
      <li>We believe that the more information you have about your condition and options for treatment, the better decisions we will make together as a partnership, and the better the outcomes for you. To this end, we have a large amount of information on the practice website, and encourage you to use this.</li>
      <li>Your Family Doctor/referring practitioner is central to all of your care. After each consultation or treatment, we will ensure that he/she is sent communication on the same day.</li>
      <li>If there is anything that we could do better, please let us know. Our practice is Your practice.</li>
    </ul>
    <div class="diagram" style="left:36px;top:428px" role="img" aria-label="Anatomical illustration of prostate cancer stages"></div>
    <div class="diagram" style="left:196px;top:428px;background:linear-gradient(150deg,#fbf6ef,#eadfcf)" role="img" aria-label="Anatomical line drawing of the bladder and prostate"></div>
    <div class="diagram" style="left:356px;top:428px" role="img" aria-label="Anatomical illustration of the testes"></div>
    <div class="diagram" style="left:36px;top:572px" role="img" aria-label="Cross-section illustration of the female pelvis"></div>
    <div class="diagram" style="left:196px;top:572px" role="img" aria-label="Cross-section illustration of the kidney"></div>
    <div class="diagram" style="left:356px;top:572px" role="img" aria-label="Cross-section illustration of the male pelvis"></div>
    <div class="abs inner-rule"></div>
  </div>

  <div class="page page--right gps">
    <div class="ph organs" role="img" aria-label="Illustration of human internal organs floating over a clinical background"></div>
    <h2 class="abs title">FOR <span>GPS</span></h2>
    <div class="abs gps-links">
      <div><span class="pill">Make a Referral</span><div class="small-tick">GP Referral Form</div></div>
      <div><span class="pill">Urological Procedures</span><div class="small-tick">Urological Procedures</div></div>
      <div><span class="pill">Contact Harbour Point Clinic</span><div class="small-tick">GP Referral Form</div></div>
    </div>
    <span class="abs pill" style="left:36px;top:364px">Help with Urology Problems</span>
    <ul class="abs ticks problems-a">
      <li>Epididymal Cysts</li><li>Epididymitis</li><li>Erectile Dysfunction</li><li>Haematospermia</li><li>Hydrocoele</li><li>Incontinence in Women</li><li>Inflammation of the Foreskin / Balanitis</li><li>Microscopic Haematuria</li><li>Nocturnal Incontinence</li><li>Paraphimosis/Foreskin</li><li>Stuck Behind Glans</li><li>Penile Curvature</li>
    </ul>
    <ul class="abs ticks problems-b">
      <li>Premature Ejaculation</li><li>Priapism</li><li>Retrograde Ejaculation</li><li>Screening for Prostate Cancer with PSA</li><li>Sterile Pyuria</li><li>Testosterone Deficiency / Hypogonadism</li><li>Tight Foreskin/Phimosis</li><li>Urethral Catheter Problems</li><li>Urinary Tract Infection in Men</li><li>Urinary Tract Infection in Women</li><li>Varicocoele (Adults)</li>
    </ul>
    <div class="ph kidneys" role="img" aria-label="Illustration of kidneys, ureters and bladder"></div>
    <div class="abs gps-contact">
      <div class="call">Call to<strong>Daniel Hartley</strong></div>
      <span class="or">-</span>
      <span class="phone">0400 118 204</span>
      <span class="or">OR</span>
      <span class="phone">0400 118 597</span>
    </div>
    <div class="abs gps-footer">www.harbourpointclinic.com.au</div>
  </div>
</section>

</body>
</html>
```